Glen Whitmore Professional Coaching

I would like a website with a mountain theme geared towards professional executives reaching higher peaks and goals. This is a 3 page website with brand essence information on the opening page, the coaching process on a second page and "about me" and lead capture form on a third page

Target Market(s)

C-Level audience, involved in tech, government, manufacturing, and transportation type of corporations

Coding

Coded - Design and coding required

Number of Pages Required

3 page

Font styles to use
Sans Serif

Colors
a7a7a7
1b1b1b
e8e8e8
3176b5
abd036
0355a3

Requirements
Must have
• Looking for a user friendly site that I can manage/update going forward. Must have:
• 1. "Is coaching right for you?" - page 1
• 2. "Our Process" page 2 - I will describe how we approach coaching
• 3. "Contact us" page 3 where I can capture contact information from potential clients
• 4. Clean and professional with more modern font
• 5. Links to personal social media sites
• 6. Ability to upload/download .pdf documents as resources
• 7. Ability to add on new pages in the future (such as a blog page)
Nice to have
• I want a place to store articles I write or use.
• LinkedIn or Twitter Feed
Should not have
• Not fluffy or too 'zen' like personal life coaches tend to present.

```html
<!DOCTYPE html>
<html lang="en">
<head>
<meta charset="utf-8">
<title>Glen Whitmore Professional Coaching</title>
<link href="https://fonts.googleapis.com/css2?family=Lato:wght@400;700;900&display=swap" rel="stylesheet">
<style>
  :root {
    --teal: #36b3b8;
    --teal-light: #72cdd1;
    --teal-pale: #a9e0e2;
    --ink: #1b1b1b;
    --text: #333333;
    --grey: #a7a7a7;
    --grey-light: #e8e8e8;
    --white: #ffffff;
    --field-border: #c9c9c9;
  }
  * { box-sizing: border-box; margin: 0; padding: 0; }
  html, body { width: 1200px; height: 2296px; overflow: hidden; }
  body {
    position: relative;
    background: var(--white);
    font-family: "Lato", Arial, sans-serif;
    color: var(--text);
  }
  .backdrop { position: absolute; left: 0; top: 0; width: 1200px; height: 2296px; }

  /* Header */
  .site-header { position: absolute; left: 0; top: 0; width: 1200px; height: 100px; }
  .brand {
    position: absolute; left: 158px; top: 36px;
    font-weight: 700; color: var(--ink); line-height: 1;
  }
  .brand-name { display: block; font-size: 31px; letter-spacing: -0.3px; }
  .brand-tag { display: block; font-size: 17.5px; letter-spacing: 2.2px; margin-top: 6px; padding-left: 3px; }
  .main-nav { position: absolute; top: 55px; left: 592px; display: flex; gap: 0; }
  .main-nav a {
    font-size: 17.5px; font-weight: 700; color: var(--ink);
    text-decoration: none; margin-right: 44px; letter-spacing: 0.2px;
  }
  .main-nav a.is-active { color: var(--teal); }

  /* Hero */
  .hero-title {
    position: absolute; left: 0; width: 1200px; top: 268px;
    text-align: center; font-weight: 900; line-height: 1.02;
  }
  .hero-title .line-main { display: block; font-size: 46px; color: var(--ink); }
  .hero-title .line-accent { display: block; font-size: 40px; color: var(--teal); margin-top: 2px; }
  .hero-lead {
    position: absolute; left: 300px; width: 600px; top: 376px;
    text-align: center; font-size: 19.5px; line-height: 28px; color: #2a2a2a;
  }
  .slider-arrow {
    position: absolute; top: 322px; width: 54px; height: 54px;
    border-radius: 50%; background: #5f5f5f;
  }
  .slider-arrow svg { position: absolute; left: 17px; top: 17px; }
  .slider-arrow.prev { left: 118px; }
  .slider-arrow.next { left: 1013px; }

  /* About */
  .portrait {
    position: absolute; left: 150px; top: 690px; width: 392px; height: 480px;
    background: linear-gradient(180deg, #d8b9a3 0%, #c9a48c 22%, #27375c 40%, #1f2c4b 100%);
    border-radius: 160px 160px 40px 40px;
  }
  .about { position: absolute; left: 592px; top: 760px; width: 450px; }
  .section-title { font-weight: 700; line-height: 1; }
  .about .section-title { font-size: 37px; color: var(--teal); }
  .about p { font-size: 16.5px; line-height: 27.3px; color: var(--text); margin-top: 25px; }
  .btn {
    display: inline-block; text-align: center; text-decoration: none;
    font-weight: 700; border-radius: 26px; letter-spacing: 0.3px;
  }
  .btn-outline {
    position: absolute; left: 592px; top: 1037px; width: 165px; height: 51px; line-height: 47px;
    border: 2px solid var(--teal); color: var(--teal); font-size: 15.5px; background: var(--white);
  }

  /* Coaching process */
  .process { position: absolute; left: 164px; top: 1262px; width: 460px; color: var(--white); }
  .process .section-title { font-size: 34px; }
  .process p { font-size: 18px; line-height: 30px; margin-top: 29px; }
  .btn-solid {
    position: absolute; left: 158px; top: 1520px; width: 175px; height: 53px; line-height: 53px;
    background: var(--white); color: #1f84b0; font-size: 17px;
  }
  .process-ring {
    position: absolute; left: 643px; top: 1187px; width: 460px; height: 460px;
    border-radius: 50%; background: var(--teal-light);
  }
  .process-ring-inner {
    position: absolute; left: 680px; top: 1220px; width: 420px; height: 420px;
    border-radius: 50%; background: var(--teal);
  }
  .process-photo {
    position: absolute; left: 700px; top: 1238px; width: 384px; height: 384px;
    border-radius: 50%;
    background: radial-gradient(circle at 50% 45%, #c9a487 0%, #8a7668 40%, #5a6b86 75%, #e3e3e5 100%);
  }

  /* Contact */
  .contact-title {
    position: absolute; left: 0; width: 1200px; top: 1738px;
    text-align: center; font-size: 31px; font-weight: 700; color: #000;
  }
  .contact-form { position: absolute; left: 196px; top: 1802px; width: 808px; height: 230px; }
  .field {
    position: absolute; background: var(--white); border: 1px solid var(--field-border);
    font-family: "Lato", Arial, sans-serif; font-size: 14.5px; color: #555;
    padding: 0 16px; outline: none;
  }
  .field::placeholder { color: #555; }
  .field-name { left: 0; top: 0; width: 400px; height: 46px; }
  .field-email { left: 0; top: 54px; width: 400px; height: 46px; }
  .field-phone { left: 0; top: 107px; width: 400px; height: 46px; }
  .field-message { left: 409px; top: 0; width: 399px; height: 153px; padding-top: 14px; resize: none; }
  .btn-send {
    position: absolute; left: 332px; top: 178px; width: 152px; height: 48px;
    border: none; border-radius: 24px; cursor: pointer;
    background: linear-gradient(180deg, #3cc0c3 0%, #2a9ea4 100%);
    color: var(--white); font-family: "Lato", Arial, sans-serif; font-size: 19px; font-weight: 400;
  }

  /* Footer */
  .site-footer { position: absolute; left: 0; top: 2160px; width: 1200px; text-align: center; }
  .copyright { font-size: 17px; color: #333; }
  .social { display: flex; justify-content: center; gap: 7px; margin-top: 18px; }
  .social a { display: block; width: 32px; height: 32px; border-radius: 50%; }
  .social .s1 { background: #3b5b99; }
  .social .s2 { background: #4fa3e0; }
  .social .s3 { background: #3d5a7a; }
  .social .s4 { background: #1769a8; }
</style>
</head>
<body>

<svg class="backdrop" width="1200" height="2296" viewBox="0 0 1200 2296" aria-hidden="true">
  <defs>
    <linearGradient id="heroSky" x1="0" y1="0" x2="0" y2="1">
      <stop offset="0" stop-color="#f0f0f0"/>
      <stop offset="0.45" stop-color="#dcdcdc"/>
      <stop offset="1" stop-color="#c2c2c2"/>
    </linearGradient>
    <linearGradient id="contactSky" x1="0" y1="0" x2="0" y2="1">
      <stop offset="0" stop-color="#d6d6d6"/>
      <stop offset="0.6" stop-color="#cbcbcb"/>
      <stop offset="1" stop-color="#b9b9b9"/>
    </linearGradient>
  </defs>

  <!-- hero band -->
  <rect x="0" y="0" width="1200" height="720" fill="url(#heroSky)"/>
  <polygon fill="#ffffff" points="0,668 40,672 80,660 120,675 170,662 220,668 270,650 320,640 360,625 400,618 440,606 470,598 500,606 540,620 580,612 620,618 660,632 700,620 740,628 790,612 830,626 870,616 910,630 950,622 1000,636 1050,628 1100,640 1150,632 1200,640 1200,720 0,720"/>

  <!-- contact band -->
  <rect x="0" y="1620" width="1200" height="560" fill="url(#contactSky)"/>
  <polygon fill="#ffffff" points="0,2130 40,2120 80,2126 130,2110 180,2116 230,2096 270,2100 320,2086 370,2094 420,2080 470,2090 520,2072 570,2080 620,2066 670,2076 720,2060 770,2072 820,2056 860,2050 900,2062 950,2070 1000,2082 1050,2090 1100,2102 1150,2112 1200,2108 1200,2180 0,2180"/>

  <!-- teal coaching band -->
  <path fill="#36b3b8" d="M0,1142 L40,1138 L90,1146 L140,1136 L190,1144 L230,1138 L260,1150 L300,1140 L350,1132 L400,1142 L450,1136 L500,1146 L540,1140 L580,1132 L620,1138 L660,1130 L700,1140 L750,1132 L800,1138 L850,1128 L900,1136 L950,1128 L1000,1136 L1050,1126 L1100,1132 L1150,1124 L1200,1130 L1200,1652 Q760,1712 0,1630 Z"/>
</svg>

<div role="img" aria-label="Snow-capped mountain range under a pale sky, in soft greys" style="position:absolute;left:0;top:0;width:1200px;height:600px;"></div>
<div role="img" aria-label="Faint grey mountain landscape behind the contact form" style="position:absolute;left:0;top:1690px;width:1200px;height:380px;"></div>

<header class="site-header">
  <a class="brand" href="#">
    <span class="brand-name">GLEN WHITMORE</span>
    <span class="brand-tag">PROFESSIONAL COACHING</span>
  </a>
  <nav class="main-nav">
    <a class="is-active" href="#">HOME</a>
    <a href="#">ABOUT ME</a>
    <a href="#">COACHING PROCESS</a>
  </nav>
</header>

<section class="hero">
  <a class="slider-arrow prev" href="#" aria-label="Previous slide">
    <svg width="20" height="20" viewBox="0 0 20 20"><polyline points="13,3 6,10 13,17" fill="none" stroke="#ffffff" stroke-width="2.6" stroke-linecap="round" stroke-linejoin="round"/></svg>
  </a>
  <h1 class="hero-title">
    <span class="line-main">WELCOME TO GLEN WHITMORE</span>
    <span class="line-accent">PROFESSIONAL COACHING</span>
  </h1>
  <p class="hero-lead">Pellentesque faucibus Ut accumsan ultricies elit Maecenas at justo id velit placerat molestie Donec dictum</p>
  <a class="slider-arrow next" href="#" aria-label="Next slide">
    <svg width="20" height="20" viewBox="0 0 20 20"><polyline points="7,3 14,10 7,17" fill="none" stroke="#ffffff" stroke-width="2.6" stroke-linecap="round" stroke-linejoin="round"/></svg>
  </a>
</section>

<section class="about-section">
  <div class="portrait" role="img" aria-label="Portrait photo of the coach in a navy blazer and checked shirt"></div>
  <div class="about">
    <h2 class="section-title">ABOUT ME</h2>
    <p>Pellentesque faucibus Ut accumsan ultricies elit Maecenas at justo id velit placerat molestie Donec dictum lectus non odio Cras a ante vitae enim iaculis aliquam<br>Mauris nunc quam venenatis nec euismod sit amet egestas placerat est Pellentesque habitant morbi tristique senectus et netus et malesuada fames ac turpis egestas Cras id elit Integer quis urna Ut ante enim dapibus malesuada fringilla eu</p>
  </div>
  <a class="btn btn-outline" href="#">LEARN MORE</a>
</section>

<section class="process-section">
  <div class="process">
    <h2 class="section-title">COACHING PROCESS</h2>
    <p>Pellentesque faucibus Ut accumsan ultricies elit Maecenas at justo id velit placerat molestie<br>Mauris nunc quam venenatis nec euismod sit amet egestas placerat est Pellentesque habitant morbi tristique senectus et netus et malesuada fames ac turpis egestas Cras id elit Integer quis urna Ut ante enim</p>
  </div>
  <a class="btn btn-solid" href="#">LEARN MORE</a>
  <div class="process-ring"></div>
  <div class="process-ring-inner"></div>
  <div class="process-photo" role="img" aria-label="Photo of a small group seated in a circle during a coaching session"></div>
</section>

<section class="contact-section">
  <h2 class="contact-title">CONTACT US</h2>
  <form class="contact-form" action="#">
    <input class="field field-name" type="text" placeholder="Name" aria-label="Name">
    <input class="field field-email" type="email" placeholder="Email" aria-label="Email">
    <input class="field field-phone" type="tel" placeholder="Phone" aria-label="Phone">
    <textarea class="field field-message" placeholder="Message" aria-label="Message"></textarea>
    <button class="btn-send" type="submit">SEND</button>
  </form>
</section>

<footer class="site-footer">
  <p class="copyright">© 2019 Company Name&nbsp; All right reserved</p>
  <div class="social">
    <a class="s1" href="#" aria-label="Social profile 1"></a>
    <a class="s2" href="#" aria-label="Social profile 2"></a>
    <a class="s3" href="#" aria-label="Social profile 3"></a>
    <a class="s4" href="#" aria-label="Social profile 4"></a>
  </div>
</footer>

</body>
</html>
```